QRV Advisors needs a web site

We need a web site for www.qrvadvisors-example.com. QRV is a mergers and acquisition consulting company that focuses our buyer and seller services on logistics companies. We help put companies together, and help with legal and financial due diligence. We want the web site to express our service and show the logistics components. We want personalized images versus pictures of trucks and airplanes.

Our new logo uses Burgandy and grey colors. Image attached. We are not in to bold, big letters...classy, artistic, low key preferred. Confidentiality, experience, professional are what we want to express on the site.

All we expect for the first part of this project is a home page, and one subpage.  We are budgeting other funds for the technical aspects of the web site

Reason: All that I'm seeing so far is trucks, forklifts and planes. We are a legal mergers and acquisitions firm that focus on logistics. I like some of the images to say logistics, but really want it say legal, financial, and putting companies together. Will pay extra for the sub page if someone can impress us with a home page.

Reason: Swamped with another project at the moment...will work on this over the weekend and provide designer feedback and select final design by Tuesday

```html
<!DOCTYPE html>
<html lang="en">
<head>
<meta charset="utf-8">
<title>QRV Advisors</title>
<link href="https://fonts.googleapis.com/css2?family=Open+Sans:wght@300;400;600;700&display=swap" rel="stylesheet">
<style>
:root{
  --crimson:#a8123a;
  --crimson-dark:#8a0d2f;
  --charcoal:#262324;
  --charcoal-deep:#1d1b1c;
  --ink:#222;
  --body:#555;
  --muted:#999;
  --hero-grey:#e4e4e4;
  --section-grey:#ededed;
  --line:#dcdcdc;
  --white:#fff;
}
*{box-sizing:border-box;margin:0;padding:0}
html,body{width:693px;height:1200px;overflow:hidden}
body{position:relative;background:var(--white);font-family:"Open Sans",Arial,sans-serif;color:var(--body)}
.abs{position:absolute}

/* header */
.site-header svg{position:absolute;left:0;top:0}
.brand{left:65px;top:18px;color:var(--white);z-index:2}
.brand-mark{display:flex;align-items:center;gap:8px}
.brand-square{width:14px;height:14px;background:var(--crimson)}
.brand-name{font-size:38px;font-weight:300;letter-spacing:6px;line-height:1}
.brand-tag{font-size:6px;color:var(--crimson);margin-top:4px;letter-spacing:.2px}
.main-nav{left:250px;top:20px;display:flex;z-index:2}
.main-nav a{font-size:8px;color:var(--white);text-decoration:none;padding:4px 12px 6px;border-right:1px solid #555;border-bottom:1px solid var(--crimson)}
.main-nav a:first-child{padding-left:6px}
.main-nav a:last-child{border-right:0}
.main-nav a.active{color:#e0315c}

/* hero */
.hero-bg{left:0;top:0;width:693px;height:372px;background:var(--hero-grey)}
.hero-art{left:300px;top:108px;width:292px;height:244px;border-radius:50% 40% 6px 6px;background:radial-gradient(circle at 40% 40%,#cfcfcf,#9a9a9a 60%,#5a5a5a)}
.hero-title{left:64px;top:153px;font-size:21px;font-weight:300;color:var(--crimson);letter-spacing:-.6px;white-space:nowrap;z-index:2}
.hero-title b{font-weight:700}
.hero-text{left:68px;top:192px;width:205px;font-size:7.6px;line-height:14.5px;color:#444;z-index:2}
.btn{display:inline-block;font-size:7.5px;text-decoration:none;text-align:center}
.btn-red{background:var(--crimson);color:var(--white)}
.btn-dark{background:var(--charcoal-deep);color:var(--white);border:1px solid #000;border-radius:2px}
.btn-light{background:var(--white);color:#222;border:1px solid #bbb;border-radius:2px}
.hero-btn{left:68px;top:263px;width:57px;height:21px;line-height:21px;z-index:2}

/* services */
.section-title{width:693px;text-align:center;font-size:15px;font-weight:600;color:var(--ink)}
.services-title{top:388px}
.service-card{top:463px;width:124px;height:140px;background:var(--white);border:1px solid var(--line);text-align:center;box-shadow:0 8px 8px -6px rgba(0,0,0,.12)}
.service-card h3{font-size:9.5px;font-weight:400;color:var(--ink);margin:19px 10px 0;padding-bottom:6px;border-bottom:1px solid var(--line)}
.service-card p{font-size:7px;line-height:11.3px;color:var(--muted);margin:6px 8px 0}
.service-card .btn{position:absolute;left:34px;top:116px;width:55px;height:18px;line-height:17px}
.service-card.featured{background:var(--charcoal-deep);border-color:var(--charcoal-deep)}
.service-card.featured h3{color:var(--white);border-color:#444}
.service-card.featured p{color:#ccc}
.service-card.featured .btn{border:0;border-radius:0}
.service-icon{top:424px;width:52px;height:52px;border-radius:50%;background:var(--white);border:1px solid var(--line);display:flex;align-items:center;justify-content:center}
.service-icon.featured{background:var(--crimson);border:2px solid var(--white);box-shadow:0 0 0 1px var(--crimson)}

/* about */
.about-band{left:0;top:637px;width:693px;height:218px;background:var(--section-grey)}
.about-title{left:64px;top:647px;font-size:14px;font-weight:300;color:var(--ink)}
.about-title b{font-weight:600}
.about-photo{left:64px;top:675px;width:121px;height:86px;border:1px solid #ccc;background:linear-gradient(180deg,#f2f2f2,#6c6c6c 70%,#2b2b2b)}
.about-text{font-size:7.2px;line-height:10.5px;color:#555}
.about-text.side{left:192px;top:677px;width:212px}
.about-text.full{left:67px;top:767px;width:335px}
.about-btn{left:66px;top:815px;width:53px;height:18px;line-height:17px}
.divider-v{left:416px;top:650px;width:1px;height:192px;background:var(--line)}
.special-title{left:435px;top:647px;font-size:14px;font-weight:400;color:var(--ink)}
.special-list{left:435px;top:680px;list-style:none}
.special-list li{font-size:7.2px;color:#555;height:18.7px;padding-left:12px;position:relative}
.special-list li::before{content:"";position:absolute;left:0;top:1px;width:5px;height:5px;border:1.5px solid var(--crimson);border-radius:50%}
.special-btn{left:448px;top:821px;width:53px;height:17px;line-height:16px}

/* testimonials + footer */
.dark-band{left:0;top:855px;width:693px;height:345px;background:var(--charcoal);border-top:3px solid var(--crimson)}
.testimonials-title{top:876px;color:var(--white);font-weight:400;font-size:13px}
.client-avatar{left:325px;top:897px;width:38px;height:38px;border-radius:50%;border:2px solid var(--crimson);background:radial-gradient(circle at 50% 40%,#d9b89a,#8a6a52)}
.quote{left:118px;top:940px;width:458px;text-align:center;font-size:9.5px;line-height:15.5px;color:#eee}
.quote .mark{font-family:Georgia,serif;font-size:20px;line-height:0;font-weight:700;vertical-align:-6px}
.footer-rule{left:78px;top:1031px;width:546px;height:1px;background:#3a3738}
.footer-col{top:1032px}
.footer-col h4{font-size:9.5px;font-weight:400;color:var(--white);margin:0 0 14px}
.footer-col p,.footer-col li{font-size:7.3px;line-height:9.5px;color:#ddd;list-style:none}
.footer-col li{line-height:11.6px}
.col-sep{top:1032px;width:1px;height:95px;background:#3a3738}
.social{display:flex;flex-wrap:wrap;gap:3px;width:82px;margin-top:8px}
.social span{width:17px;height:17px;border-radius:50%;background:var(--white)}
.contact-row{display:flex;gap:6px;align-items:flex-start;margin-bottom:4px}
.contact-row svg{flex:none;margin-top:1px}
.map{left:489px;top:1053px;width:135px;height:79px;background:linear-gradient(135deg,#e8e4da,#d6d2c6)}
.bottom-bar{left:0;top:1166px;width:693px;height:34px;background:var(--charcoal-deep)}
.copyright{top:1179px;width:693px;text-align:center;font-size:7.3px;color:#bbb}
</style>
</head>
<body>

<div class="abs hero-bg"></div>
<div class="abs hero-art" role="img" aria-label="Globe with plane, van, truck and cargo ship beside a smiling businessman in a grey suit"></div>
<svg class="abs" style="left:0;top:330px" width="693" height="45" viewBox="0 0 693 45">
  <path d="M0 8 Q346 40 693 6 L693 45 L0 45 Z" fill="#fff"/>
  <path d="M0 8 Q346 40 693 6" fill="none" stroke="#d0d0d0" stroke-width="1.5"/>
</svg>

<header class="site-header">
  <svg width="693" height="110" viewBox="0 0 693 110">
    <polygon points="0,0 693,0 693,24 116,96 0,68" fill="#262324"/>
    <polygon points="116,96 693,24 693,36 116,102" fill="#a8123a"/>
    <polygon points="0,68 116,96 116,102 0,74" fill="#8a0d2f"/>
  </svg>
  <div class="abs brand">
    <div class="brand-mark"><span class="brand-name">QRV</span><span class="brand-square"></span></div>
    <div class="brand-tag">Mergers &amp; Acquisitions Consulting Services</div>
  </div>
  <nav class="abs main-nav">
    <a class="active" href="#">HOME</a><a href="#">About</a><a href="#">Services</a><a href="#">News &amp; Events</a><a href="#">Contact Us</a>
  </nav>
</header>

<h1 class="abs hero-title"><b>QRV</b> PROFESSIONALS</h1>
<p class="abs hero-text">QRV assists business owners within the logistics industry to implement growth and exit strategies. We offer business planning and merger and acquisition(M&amp;A) advisory services.</p>
<a class="abs btn btn-red hero-btn" href="#">Read More</a>

<h2 class="abs section-title services-title">Our Services</h2>

<div class="abs service-card" style="left:76px"><h3>Legal Diligence</h3><p>Lorem Ipsum is simply dummy text of the printing and typesetting industry. Lorem Ipsum has been the industry's standard dummy text ever since the 1500s.</p><a class="btn btn-light" href="#">Read More</a></div>
<div class="abs service-card featured" style="left:214px"><h3>Financial Dues</h3><p>Lorem Ipsum is simply dummy text of the printing and typesetting industry. Lorem Ipsum has been the industry's standard dummy text ever since the 1500s.</p><a class="btn btn-red" href="#">Read More</a></div>
<div class="abs service-card" style="left:353px"><h3>Acquistion Consulting</h3><p>Lorem Ipsum is simply dummy text of the printing and typesetting industry. Lorem Ipsum has been the industry's standard dummy text ever since the 1500s.</p><a class="btn btn-light" href="#">Read More</a></div>
<div class="abs service-card" style="left:491px"><h3>Logistics Component</h3><p>Lorem Ipsum is simply dummy text of the printing and typesetting industry. Lorem Ipsum has been the industry's standard dummy text ever since the 1500s.</p><a class="btn btn-light" href="#">Read More</a></div>

<div class="abs service-icon" style="left:112px">
  <svg width="22" height="18" viewBox="0 0 22 18"><path d="M1 2 L10 4 L10 17 L1 15 Z M21 2 L12 4 L12 17 L21 15 Z" fill="#262324"/></svg>
</div>
<div class="abs service-icon featured" style="left:250px">
  <svg width="18" height="20" viewBox="0 0 18 20"><path d="M6 1 L12 1 L10 5 Q17 9 16 16 Q15 19 9 19 Q3 19 2 16 Q1 9 8 5 Z" fill="#fff"/><text x="9" y="16" font-size="8" text-anchor="middle" fill="#a8123a" font-family="Open Sans, sans-serif" font-weight="700">$</text></svg>
</div>
<div class="abs service-icon" style="left:389px">
  <svg width="24" height="18" viewBox="0 0 24 18"><circle cx="7" cy="5" r="3" fill="#262324"/><circle cx="17" cy="5" r="3" fill="#262324"/><circle cx="12" cy="4" r="3.4" fill="#262324"/><path d="M2 17 Q2 9 7 9 Q12 9 12 17 Z M12 17 Q12 9 17 9 Q22 9 22 17 Z M6 17 Q6 8 12 8 Q18 8 18 17 Z" fill="#262324"/></svg>
</div>
<div class="abs service-icon" style="left:527px">
  <svg width="24" height="20" viewBox="0 0 24 20"><rect x="8" y="2" width="14" height="9" fill="#262324"/><path d="M1 6 L7 6 L7 11 L1 11 Z" fill="#262324"/><circle cx="4" cy="12" r="2" fill="#262324"/><circle cx="18" cy="12" r="2" fill="#262324"/><text x="16" y="20" font-size="7" text-anchor="middle" fill="#262324" font-family="Open Sans, sans-serif" font-weight="700">$</text></svg>
</div>

<div class="abs about-band"></div>
<h2 class="abs about-title">Welcome to <b>Quiet River Ventures</b></h2>
<div class="abs about-photo" role="img" aria-label="Team of five business professionals in dark suits"></div>
<p class="abs about-text side">QRV assists business owners within the logistics industry to implement growth and exit strategies. We offer business planning and merger and acquisition(M&amp;A) advisory services. QRV services are offered by industry executives with extensive M&amp;A experience. Your company will benefit from a unique and outside perspective from consultants that understand your business.</p>
<p class="abs about-text full">QRV can help you formulate and execute your growth strategy. We take a strategic and consultative approach with our advisory services that will help you grow your business effectively. Since our experience and focus is only in the logistics space, you can be confident that our process will be efficient and streamlined as we help achieve your goals.</p>
<a class="abs btn btn-dark about-btn" href="#">Read More</a>

<div class="abs divider-v"></div>
<h2 class="abs special-title">Our Speacial Services</h2>
<ul class="abs special-list">
  <li>Lorem ipsum dolor sit amet, consectetur adipisicing.</li>
  <li>Lorem ipsum dolor sit amet.</li>
  <li>Lorem ipsum dolor sit amet, consectetur.</li>
  <li>Lorem ipsum dolor sit amet, consectetur adipisicing.</li>
  <li>Lorem ipsum dolor sit amet.</li>
  <li>Lorem ipsum dolor sit amet, consectetur.</li>
  <li>Lorem ipsum dolor sit amet, consectetur adipisicing.</li>
</ul>
<a class="abs btn btn-dark special-btn" href="#">View All</a>

<div class="abs dark-band"></div>
<h2 class="abs section-title testimonials-title">Clients Testimonials</h2>
<div class="abs client-avatar" role="img" aria-label="Portrait of a client"></div>
<p class="abs quote"><span class="mark">&ldquo;</span>Lorem ipsum dolor sit amet, consectetur adipisicing elit, sed do eiusmod tempor incididunt ut labore et dolore magna aliqua. Ut enim ad minim veniam, quis nostrud exercitation ullamco laboris nisi ut aliquip ex ea commodo consequat.<span class="mark">&rdquo;</span></p>

<div class="abs footer-rule"></div>
<div class="abs footer-col" style="left:78px;width:110px">
  <h4>About Us</h4>
  <p>Lorem ipsum dolor sit amet, consectetur adipisicing elit, sed do eiusmod tempor incididunt ut labore et dolore magna aliqua.</p>
  <div class="social"><span></span><span></span><span></span><span></span><span></span><span></span><span></span></div>
</div>
<div class="abs col-sep" style="left:203px"></div>
<div class="abs footer-col" style="left:226px">
  <h4>Company Information</h4>
  <ul><li>Home</li><li>About Us</li><li>Services</li><li>News &amp; Events</li><li>Contact Us</li></ul>
</div>
<div class="abs col-sep" style="left:336px"></div>
<div class="abs footer-col" style="left:358px">
  <h4>Contact Us</h4>
  <div class="contact-row"><svg width="9" height="8" viewBox="0 0 9 8"><path d="M4.5 0 L9 4 L7.5 4 L7.5 8 L1.5 8 L1.5 4 L0 4 Z" fill="#bbb"/></svg><p>P.O. Box 4410<br>Maple Grove, ST 00000</p></div>
  <div class="contact-row"><svg width="9" height="7" viewBox="0 0 9 7"><rect width="9" height="7" fill="#bbb"/><path d="M0 0 L4.5 4 L9 0" fill="none" stroke="#262324"/></svg><p>hello@qrvadvisors-example.com</p></div>
  <div class="contact-row"><svg width="9" height="9" viewBox="0 0 9 9"><path d="M2 0 L4 2 L3 3.5 Q4 5.5 5.5 6 L7 5 L9 7 L7.5 9 Q1 8 0 1.5 Z" fill="#bbb"/></svg><p>+(555) 010 2040</p></div>
</div>
<div class="abs footer-col" style="left:489px"><h4>Map</h4></div>
<div class="abs map" role="img" aria-label="Street map showing the office location"></div>

<div class="abs bottom-bar"></div>
<svg class="abs" style="left:333px;top:1144px" width="26" height="22" viewBox="0 0 26 22"><polygon points="0,22 13,8 26,22" fill="#1d1b1c"/></svg>
<p class="abs copyright">Copyright &copy; 2014 QRV. all rights reserved</p>

</body>
</html>
```